Website Design for Solar Panel Company

We are working with a company called VoltaNix.

Some sites to use for content/competitors and inspiration:
https://www.brivaloo.com
https://prod.aws-prod.kelmatrix.com
https://tovarqueworks.net
https://www.quorvex.com/solarpanels

Thank you for taking the time to consider designing a website for us. We are web developers based in Stockton, CA, USA. Most of our projects go through the same process. Understanding this process may help you win a project with us. We custom-code all of our websites in-house. We don’t have any requirements as to what tools you use for your design, but we prefer Figma files. For any design that we label as four-stars, we send it to the client for review. The client picks the final design they want us to use. Once we complete this process, we will continue to show additional clients all the four-star sites and purchase them later. Your designs will have multiple chances to sell. For better chances of success, we ask that you follow these guidelines.

IMAGES:
If you use any images or icons in the design, we ask that you have a link to the asset so we can purchase the image/icon. Most of the designs we submit do not have the customer’s images on them unless they have some great images. Be creative; show us the feeling you are trying to portray with your image choices. Use any royalty-free site you choose. We subscribe to Pendrel and mainly use their images, but we can purchase images outside of Pendrel. PLEASE NOTE: we will not submit designs to clients with watermarks on the images.

FONTS:
We ask that you identify the fonts used in the design. This can be done in a message if you want. We typically use Google Fonts and Pendrel Fonts.

CONTENT:
We're always open to different content and ideas. We often submit designs with stock images so the client can see our vision. We typically take pictures after the website launch to use their images with our vision. Lorem Ipsum is fine for paragraphs, but we ask that you write the headers in correct English. We want to be able to show the vision and identify the sections of the website.

INSPIRATION:
We typically add a couple of links in the brief of websites we like to help you get started in your design.

REVISIONS:
We do not often ask for revisions of the designs unless we see something in the design that may not appeal to the client. If there are slight changes that we want to make, we do that in the development process.

FEEDBACK:
We rarely give feedback on designs during the design process. We are working on many website projects and do not have the time to provide feedback. We usually respond if your request is well thought out and asks specific questions, but a note asking “feedback, please” usually goes unanswered.

```html
<!DOCTYPE html>
<html lang="en">
<head>
<meta charset="UTF-8">
<title>VoltaNix — Solar Energy</title>
<link href="https://fonts.googleapis.com/css2?family=Jost:wght@400;500;600;700&display=swap" rel="stylesheet">
<style>
:root{
  --green:#4cc417;
  --green-dark:#2f9e22;
  --green-light:#6ee22f;
  --black:#000;
  --ink:#111;
  --muted:#555;
  --gray-bg:#f5f5f5;
  --white:#fff;
  --sky:#6d88ab;
  --sky-dark:#3a5479;
}
*{box-sizing:border-box;margin:0;padding:0}
html,body{width:1200px;height:4546px;overflow:hidden}
body{font-family:'Jost',sans-serif;color:var(--ink);background:var(--white);position:relative}
.abs{position:absolute}
.btn{position:absolute;background:var(--black);color:var(--white);font-weight:600;display:flex;align-items:center;justify-content:center;gap:10px;text-transform:uppercase;letter-spacing:.2px}
.btn svg{width:22px;height:10px}
.underline{position:absolute;height:4px;background:var(--green)}
h2{position:absolute;font-weight:600;text-transform:uppercase;color:var(--ink)}

/* header */
.topbar{left:0;top:0;width:1200px;height:42px}
.topbar-info{top:10px;color:var(--white);font-size:14px;display:flex;align-items:center;gap:8px}
.logo{font-weight:700;letter-spacing:1px;color:var(--black)}
.nav{top:68px;font-size:20px;font-weight:500;color:var(--ink);text-transform:uppercase}

/* hero */
.hero-title{left:0;width:1200px;top:272px;text-align:center;color:var(--white);font-size:64px;font-weight:700;text-transform:uppercase}
.hero-text{left:260px;width:680px;top:380px;text-align:center;color:var(--white);font-size:19px;line-height:1.3}

/* about */
.about-text{left:581px;width:540px;font-size:13.5px;line-height:1.3;color:var(--muted)}

/* why */
.why{left:0;top:1325px;width:1200px;height:604px;background:var(--gray-bg)}
.why-img{width:291px;height:226px}
.why-label{width:226px;height:53px;background:var(--white);font-size:15px;font-weight:600;display:flex;align-items:center;justify-content:center;text-transform:uppercase;color:#222}

/* quote */
.quote{left:0;top:1929px;width:1200px;height:607px;background:linear-gradient(100deg,var(--green-dark) 0%,#45b62a 50%,var(--green-light) 100%)}
.field{position:absolute;background:var(--white);border-radius:5px;height:42px;font-size:15px;color:#666;padding:12px 18px}

/* tech */
.tech-card{left:473px;top:2796px;width:597px;height:378px;background:var(--white);box-shadow:0 10px 40px rgba(0,0,0,.12);border-bottom:6px solid var(--green)}
.tech-item{position:absolute;left:50px;width:480px;height:62px;display:flex;align-items:center;gap:16px;font-size:15.5px;color:#333;border-bottom:1px solid #e6e6e6}
.tech-item:last-child{border-bottom:none}
.tech-item svg{width:30px;height:30px}

/* faq */
.faq{left:0;top:3279px;width:1200px;height:548px;background:var(--gray-bg)}
.faq-item{position:absolute;display:flex;align-items:center;gap:12px;font-size:15px;color:#333}
.faq-item svg{width:44px;height:44px}

/* cta */
.cta{left:0;top:3827px;width:1200px;height:312px;background:linear-gradient(100deg,var(--green-dark) 0%,#45b62a 50%,var(--green-light) 100%)}

/* footer */
.footer{left:0;top:4139px;width:1200px;height:407px;background:var(--black);color:var(--white)}
.footer-nav{position:absolute;top:222px;left:0;width:1200px;display:flex;justify-content:center;font-size:20px;font-weight:500;text-transform:uppercase}
.footer-nav span{padding:0 24px;border-left:2px solid var(--green);height:54px;display:flex;align-items:center;margin-top:-14px}
.footer-nav span:first-child{border-left:none}
</style>
</head>
<body>

<!-- HEADER -->
<svg class="abs topbar" viewBox="0 0 1200 42"><polygon points="600,0 1200,0 1200,42 645,42" fill="var(--green)"/></svg>
<div class="abs topbar-info" style="left:853px">
  <svg width="14" height="14" viewBox="0 0 24 24"><path fill="#fff" d="M6.6 10.8a15 15 0 0 0 6.6 6.6l2.2-2.2c.3-.3.7-.4 1-.2 1.1.4 2.3.6 3.6.6.6 0 1 .4 1 1V20c0 .6-.4 1-1 1A17 17 0 0 1 3 4c0-.6.4-1 1-1h3.5c.6 0 1 .4 1 1 0 1.3.2 2.5.6 3.6.1.3 0 .7-.2 1z"/></svg>
  888 888 8888
</div>
<div class="abs topbar-info" style="left:1020px">
  <svg width="16" height="12" viewBox="0 0 16 12"><rect width="16" height="12" rx="1" fill="#fff"/><path d="M1 1l7 5 7-5" stroke="var(--green)" fill="none" stroke-width="1.4"/></svg>
  info@domain.com
</div>
<div class="abs logo" style="left:35px;top:34px;font-size:44px">VOLTANIX</div>
<div class="abs nav" style="left:376px">Home</div>
<div class="abs nav" style="left:494px">About Us</div>
<div class="abs nav" style="left:644px">Services</div>
<div class="abs nav" style="left:803px">Prices</div>
<div class="abs nav" style="left:921px">FAQs</div>
<div class="btn" style="left:1029px;top:63px;width:143px;height:39px;font-size:14px;font-weight:500">Contact Us
  <svg viewBox="0 0 22 10"><path d="M0 5h19M15 1l5 4-5 4" stroke="var(--green)" stroke-width="2" fill="none"/></svg></div>

<!-- HERO -->
<svg class="abs" style="left:0;top:116px" width="1200" height="660" viewBox="0 0 1200 660">
  <defs>
    <linearGradient id="heroSky" x1="0" y1="0" x2="0.6" y2="1">
      <stop offset="0" stop-color="#7b93b4"/><stop offset="0.5" stop-color="var(--sky)"/><stop offset="1" stop-color="var(--sky-dark)"/>
    </linearGradient>
    <linearGradient id="heroGreen" x1="0" y1="0" x2="1" y2="0">
      <stop offset="0" stop-color="var(--green-dark)"/><stop offset="1" stop-color="var(--green-light)"/>
    </linearGradient>
  </defs>
  <path d="M0 380 Q600 801 1200 380 V 460 Q600 801 0 530 Z" fill="url(#heroGreen)"/>
  <path d="M0 0 H1200 V378 Q600 775 0 431 Z" fill="url(#heroSky)" role="img" aria-label="Photo of a technician inspecting rows of solar panels under a blue sky"/>
</svg>
<div class="abs hero-title">VoltaNix</div>
<div class="abs hero-text">Lorem ipsum dolor sit amet, consectetur adipiscing elit, sed do eiusmod tempor incididunt ut labore et dolore magna aliqua.</div>
<div class="btn" style="left:472px;top:469px;width:219px;height:42px;font-size:20px;font-weight:500">Get a Quote
  <svg viewBox="0 0 22 10"><path d="M0 5h19M15 1l5 4-5 4" stroke="var(--green)" stroke-width="2" fill="none"/></svg></div>

<!-- ABOUT -->
<div class="abs" role="img" aria-label="Photo of a solar engineer in a hard hat at a solar farm" style="left:122px;top:863px;width:398px;height:398px;border-radius:50%;background:radial-gradient(circle at 40% 40%,#8d9aa6,#3b4a5c 75%)"></div>
<h2 style="left:581px;top:930px;font-size:42px">About Us</h2>
<div class="underline" style="left:581px;top:982px;width:113px"></div>
<p class="abs about-text" style="top:998px">Lorem ipsum dolor sit amet, consectetur adipiscing elit, sed do eiusmod tempor incididunt ut labore et doloremagna aliqua. Ut enim ad minim veniam, quis nostrud exercitation ullamco laboris nisi ut aliquip ex ea commodo consequat. Duis aute irure dolor in reprehenderit in voluptate velit esse cillum dolore eu fugiat nulla pariatur.</p>
<p class="abs about-text" style="top:1087px">Excepteur sint occaecat cupidatat non proident, sunt in culpa qui officia deserunt mollit anim id est laborum.</p>
<div class="btn" style="left:588px;top:1163px;width:164px;height:37px;font-size:15px">Get a Quote
  <svg viewBox="0 0 22 10"><path d="M0 5h19M15 1l5 4-5 4" stroke="var(--green)" stroke-width="2" fill="none"/></svg></div>

<!-- WHY CHOOSE US -->
<div class="abs why"></div>
<h2 style="left:0;width:1200px;text-align:center;top:1398px;font-size:42px">Why Choose Us</h2>
<div class="underline" style="left:551px;top:1452px;width:113px"></div>
<div class="abs why-img" role="img" aria-label="Photo of a house roof covered with solar panels" style="left:97px;top:1514px;background:linear-gradient(160deg,#9aa9b8,#4b5665)"></div>
<div class="abs why-label" style="left:129px;top:1715px">Unrivaled Home Solar</div>
<div class="abs why-img" role="img" aria-label="Illustration of a robot holding a solar panel under bright sky" style="left:454px;top:1519px;background:linear-gradient(180deg,#2f8fe0,#8fd0f5 70%,#5cb847)"></div>
<div class="abs why-label" style="left:493px;top:1719px">Smart Technology</div>
<div class="abs why-img" role="img" aria-label="Photo of hands working on a solar panel on a wooden table" style="left:810px;top:1522px;background:linear-gradient(150deg,#c49a6a,#3b3b3f 60%,#9b7450)"></div>
<div class="abs why-label" style="left:850px;top:1719px">Seamless Backup Power</div>
<div class="btn" style="left:500px;top:1842px;width:190px;height:39px;font-size:15px">More About Us
  <svg viewBox="0 0 22 10"><path d="M0 5h19M15 1l5 4-5 4" stroke="var(--green)" stroke-width="2" fill="none"/></svg></div>

<!-- QUOTE -->
<div class="abs quote"></div>
<h2 style="left:0;width:1200px;text-align:center;top:1986px;font-size:42px;color:var(--white)">Get a Quote</h2>
<div class="underline" style="left:548px;top:2040px;width:113px;background:var(--white)"></div>
<div class="field" style="left:240px;top:2112px;width:348px">Your Name</div>
<div class="field" style="left:625px;top:2112px;width:348px">Your Phone</div>
<div class="field" style="left:240px;top:2183px;width:348px">Email Address</div>
<div class="field" style="left:625px;top:2183px;width:348px">Select Service</div>
<div class="field" style="left:240px;top:2254px;width:733px;height:92px">Additional Message</div>
<div class="btn" style="left:236px;top:2373px;width:734px;height:55px;font-size:16px">Get a Free Quote Now</div>

<!-- HIGH TECH -->
<div class="abs" role="img" aria-label="Photo of solar panels beneath tall green trees" style="left:118px;top:2633px;width:542px;height:378px;background:linear-gradient(180deg,#cfdbe6 0%,#6f8a5e 45%,#8ea0b4 100%)"></div>
<div class="abs tech-card">
  <h2 style="left:38px;top:40px;font-size:42px">High Tech. Hassle Free</h2>
  <div class="underline" style="left:38px;top:92px;width:113px"></div>
  <p class="abs" style="left:38px;top:110px;width:530px;font-size:13.5px;line-height:1.3;color:var(--muted)">Lorem ipsum dolor sit amet, consectetur adipiscing elit, sed do eiusmod tempor incididunt ut labore et doloremagna aliqua. Ut enim ad minim veniam, quis nostrud exercitation ullamco laboris nisi ut aliquip ex ea commodo consequat.</p>
  <div class="tech-item" style="top:174px">
    <svg viewBox="0 0 30 30"><circle cx="15" cy="12" r="8" fill="none" stroke="var(--green)" stroke-width="1.6"/><path d="M10 19l-3 8 8-3 8 3-3-8" fill="none" stroke="var(--green)" stroke-width="1.6"/><path d="M11 12l3 3 5-5" fill="none" stroke="var(--green)" stroke-width="1.6"/></svg>
    Best-in-class solar panels and battery storage</div>
  <div class="tech-item" style="top:236px">
    <svg viewBox="0 0 30 30"><circle cx="15" cy="15" r="6" fill="none" stroke="var(--green)" stroke-width="1.6"/><path d="M15 2v5M15 23v5M2 15h5M23 15h5M6 6l3 3M21 21l3 3M24 6l-3 3M9 21l-3 3" stroke="var(--green)" stroke-width="1.6"/></svg>
    25-year equipment guarantee</div>
  <div class="tech-item" style="top:298px">
    <svg viewBox="0 0 30 30"><rect x="4" y="14" width="22" height="12" fill="none" stroke="var(--green)" stroke-width="1.6"/><path d="M4 20h22M11 14v12M19 14v12M15 4v6M10 8h10" stroke="var(--green)" stroke-width="1.6"/></svg>
    High tech equipments</div>
</div>

<!-- FAQ -->
<div class="abs faq"></div>
<h2 style="left:76px;top:3356px;font-size:42px">Frequently Asked Questions</h2>
<div class="underline" style="left:80px;top:3410px;width:113px"></div>
<div class="faq-item" style="left:87px;top:3492px"><svg viewBox="0 0 44 44"><circle cx="22" cy="22" r="22" fill="var(--green)"/><path d="M18 13l9 9-9 9" stroke="#fff" stroke-width="2.4" fill="none"/></svg>Lorem ipsum dolor sit amet, consectetur adipiscing elit.</div>
<div class="faq-item" style="left:645px;top:3492px"><svg viewBox="0 0 44 44"><circle cx="22" cy="22" r="22" fill="var(--green)"/><path d="M18 13l9 9-9 9" stroke="#fff" stroke-width="2.4" fill="none"/></svg>Lorem ipsum dolor sit amet, consectetur adipiscing elit.</div>
<div class="faq-item" style="left:87px;top:3578px"><svg viewBox="0 0 44 44"><circle cx="22" cy="22" r="22" fill="var(--green)"/><path d="M18 13l9 9-9 9" stroke="#fff" stroke-width="2.4" fill="none"/></svg>Lorem ipsum dolor sit amet, consectetur adipiscing elit.</div>
<div class="faq-item" style="left:645px;top:3578px"><svg viewBox="0 0 44 44"><circle cx="22" cy="22" r="22" fill="var(--green)"/><path d="M18 13l9 9-9 9" stroke="#fff" stroke-width="2.4" fill="none"/></svg>Lorem ipsum dolor sit amet, consectetur adipiscing elit.</div>
<div class="faq-item" style="left:87px;top:3665px"><svg viewBox="0 0 44 44"><circle cx="22" cy="22" r="22" fill="var(--green)"/><path d="M18 13l9 9-9 9" stroke="#fff" stroke-width="2.4" fill="none"/></svg>Lorem ipsum dolor sit amet, consectetur adipiscing elit.</div>
<div class="faq-item" style="left:645px;top:3665px"><svg viewBox="0 0 44 44"><circle cx="22" cy="22" r="22" fill="var(--green)"/><path d="M18 13l9 9-9 9" stroke="#fff" stroke-width="2.4" fill="none"/></svg>Lorem ipsum dolor sit amet, consectetur adipiscing elit.</div>

<!-- CTA -->
<div class="abs cta"></div>
<h2 style="left:0;width:1200px;text-align:center;top:3880px;font-size:42px;color:var(--white)">Get Ready to Start?</h2>
<div class="underline" style="left:538px;top:3944px;width:113px;background:var(--white)"></div>
<p class="abs" style="left:280px;width:640px;top:3970px;text-align:center;font-size:16px;line-height:1.35;color:var(--white)">Lorem ipsum dolor sit amet, consectetur adipiscing elit, sed do eiusmod tempor incididunt ut labore et doloremagna aliqua.</p>
<div class="btn" style="left:508px;top:4049px;width:190px;height:39px;font-size:15px">Contact Us
  <svg viewBox="0 0 22 10"><path d="M0 5h19M15 1l5 4-5 4" stroke="var(--green)" stroke-width="2" fill="none"/></svg></div>

<!-- FOOTER -->
<div class="abs footer">
  <div class="abs logo" style="left:0;width:1200px;text-align:center;top:84px;font-size:60px;color:var(--white)">VOLTANIX</div>
  <div class="footer-nav"><span>Home</span><span>About Us</span><span>Services</span><span>Prices</span><span>FAQs</span></div>
  <div class="abs" style="left:427px;top:288px;font-size:17px;display:flex;align-items:center;gap:10px">
    <svg width="16" height="16" viewBox="0 0 24 24"><path fill="var(--green)" d="M6.6 10.8a15 15 0 0 0 6.6 6.6l2.2-2.2c.3-.3.7-.4 1-.2 1.1.4 2.3.6 3.6.6.6 0 1 .4 1 1V20c0 .6-.4 1-1 1A17 17 0 0 1 3 4c0-.6.4-1 1-1h3.5c.6 0 1 .4 1 1 0 1.3.2 2.5.6 3.6.1.3 0 .7-.2 1z"/></svg>888 888 8888</div>
  <div class="abs" style="left:622px;top:288px;font-size:17px;display:flex;align-items:center;gap:12px">
    <svg width="18" height="13" viewBox="0 0 16 12"><rect width="16" height="12" rx="1" fill="var(--green)"/><path d="M1 1l7 5 7-5" stroke="#000" fill="none" stroke-width="1.2"/></svg>info@domain.com</div>
  <div class="abs" style="left:0;width:1200px;text-align:center;top:349px;font-size:10px;color:#ddd">Copyright 2024 VoltaNix. All Rights Reserved.</div>
</div>

</body>
</html>
```